Building company buisness cards

We are looking for a sharp modern new look for our business cards.
We are a New Zealand based company that specialises in house and land packages.
We have attached a photo of the current logo and would like to see if it can be improved somehow if needed.
We are open to any colours but we have chosen green at this stage.
Feel free to change the font and make the logo smarter looking.
Play with the colours and see what looks best.

We want a card that looks so good know one will want to throw it away!

Target Market(s)

Home buyers

Industry/Entity Type

Building

Contact Information for Business Card

Derek Tolvane
0217394062
dtolvane@quillmarkhomesteads.co.nz
quillmarkhomesteads.co.nz

Font styles to use
Serif
Sans Serif

Colors

Designer to choose colors to be used in the design.

Requirements
Must have
• Logo and company name on one side, details on the other side
Nice to have
• Color codes for the original green are HEX #4a8028, RGB(74,128,40), CMYK(42,0,69,50)
• Round corners, Raised and/or spot UV

```html
<!DOCTYPE html>
<html lang="en">
<head>
<meta charset="utf-8">
<title>Quillmark Homesteads – Business Cards</title>
<link rel="stylesheet" href="https://fonts.googleapis.com/css2?family=Arimo:wght@400;700&family=Source+Sans+3:wght@400&display=swap">
<style>
  :root {
    --brand-green: #4a8028;
    --swoosh-grey: #6b6b6b;
    --backdrop: #c9cacc;
    --card-white: #ffffff;
    --ink-dark: #2a2a2a;
  }
  * { box-sizing: border-box; margin: 0; padding: 0; }
  html, body { width: 1200px; height: 1015px; overflow: hidden; }
  body { background: var(--backdrop); position: relative; font-family: "Source Sans 3", "Myriad Pro", sans-serif; }

  .card {
    position: absolute;
    background: var(--card-white);
    overflow: hidden;
    box-shadow: 0 3px 8px rgba(0,0,0,0.25);
  }
  .card-front { left: 98px; top: 79px; width: 688px; height: 393px; border-radius: 20px; }
  .card-back { left: 429px; top: 544px; width: 687px; height: 392px; border-radius: 34px; }

  .front-waves { position: absolute; inset: 0; width: 100%; height: 100%; }

  .wordmark {
    position: absolute;
    left: 0; right: 0;
    text-align: center;
    font-family: "Arimo", Arial, sans-serif;
    font-weight: 700;
    color: var(--brand-green);
    line-height: 1.05;
    letter-spacing: -0.5px;
  }
  .card-front .wordmark { top: 92px; font-size: 32px; }
  .card-back .wordmark { top: 170px; font-size: 44px; }

  .rule { position: absolute; height: 2px; background: var(--brand-green); }
  .card-front .rule { left: 270px; width: 120px; top: 181px; }
  .card-back .rule { left: 256px; width: 152px; top: 285px; }

  .holder-name {
    position: absolute; left: 0; right: 0; top: 204px;
    text-align: center;
    font-family: "Arimo", Arial, sans-serif;
    font-weight: 700; font-size: 26px;
    color: var(--brand-green);
  }

  .contact { position: absolute; left: 0; right: 0; color: #fff; display: flex; justify-content: center; align-items: center; }
  .contact svg { flex: none; }
  .contact-phone { top: 308px; font-size: 22px; gap: 7px; padding-right: 30px; }
  .contact-lines { top: 347px; font-size: 16px; gap: 8px; letter-spacing: -0.2px; padding-left: 8px; }
  .contact-lines .spacer { width: 10px; }

  .back-url {
    position: absolute; left: 0; right: 0; top: 343px;
    text-align: center; font-size: 17px; letter-spacing: 2.2px;
    color: var(--ink-dark);
  }
  .back-url .domain { color: var(--brand-green); }
</style>
</head>
<body>

<section class="card card-front" aria-label="Card front with contact details">
  <svg class="front-waves" viewBox="0 0 688 393" preserveAspectRatio="none" aria-hidden="true">
    <path d="M0,176 C150,250 360,300 557,261 C380,285 180,268 0,205 Z" fill="var(--swoosh-grey)"/>
    <path d="M0,213 C200,300 450,325 688,216 L688,393 L0,393 Z" fill="var(--brand-green)"/>
  </svg>

  <div class="wordmark">quillmark<br>homesteads.</div>
  <div class="rule"></div>
  <div class="holder-name">Derek Tolvane</div>

  <div class="contact contact-phone">
    <svg width="19" height="19" viewBox="0 0 20 20" aria-hidden="true">
      <circle cx="10" cy="10" r="8.5" fill="none" stroke="#fff" stroke-width="1.4"/>
      <path d="M7.5,5.5 L9.5,7.5 L8.5,9 C9,10.5 10,11.5 11,12 L12.5,11 L14.5,13 L13,14.5 C9.5,14 6,10.5 5.5,7 Z" fill="#fff"/>
    </svg>
    <span>0217394062</span>
  </div>

  <div class="contact contact-lines">
    <svg width="16" height="13" viewBox="0 0 16 13" aria-hidden="true">
      <path d="M1,5 L8,1 L15,5 L15,12 L1,12 Z" fill="#fff"/>
      <path d="M1,5 L8,9 L15,5" fill="none" stroke="var(--brand-green)" stroke-width="1.2"/>
    </svg>
    <span>dtolvane@quillmarkhomesteads.co.nz</span>
    <span class="spacer"></span>
    <svg width="15" height="15" viewBox="0 0 16 16" aria-hidden="true" fill="none" stroke="#fff" stroke-width="1">
      <circle cx="8" cy="8" r="7"/>
      <ellipse cx="8" cy="8" rx="3" ry="7"/>
      <path d="M1,8 H15 M2.5,4.5 H13.5 M2.5,11.5 H13.5"/>
    </svg>
    <span>www.quillmarkhomesteads.co.nz</span>
  </div>
</section>

<section class="card card-back" aria-label="Card back with company name">
  <div class="wordmark">quillmark<br>homesteads.</div>
  <div class="rule"></div>
  <div class="back-url">www.<span class="domain">quillmarkhomesteads</span>.co.nz</div>
</section>

</body>
</html>
```